Bulldog themed background for Real Estate Purchase Letter

I need a phantom background or watermark on a standard 8 1/2" x 11" paper. I am going to put a letter over the background. I want a bulldog theme that is cute, funny and original. This letter is for a real estate project and we want to capture the person sub-consciously . Attached is my personal dogs. If you want to use them you can but not required. I have attached the letter that I am trying to emulate. I want bulldogs not horses.

Target Market(s)

45 years old and higher

Industry/Entity Type

Real Estate

Font styles to use
Serif
Sans Serif

Colors

Designer to choose colors to be used in the design.

Requirements
Must have
• fun, happiness, reassuring,
Should not have
• violence, negativity, unhappy

```html
<!DOCTYPE html>
<html lang="en">
<head>
<meta charset="utf-8">
<title>Purchase Letter – Bulldog Letterhead</title>
<link href="https://fonts.googleapis.com/css2?family=Didact+Gothic&family=Roboto:wght@400&family=EB+Garamond:wght@500&display=swap" rel="stylesheet">
<style>
  :root {
    --backdrop: #e6e6e6;
    --brand-blue: #0b4f9c;
    --paper-tint-a: #d3d8cf;
    --paper-tint-b: #bcc6b4;
    --ink: #2f2f2f;
    --ink-soft: #5a5a5a;
  }
  html, body {
    margin: 0;
    width: 1024px;
    height: 1200px;
    overflow: hidden;
    background: var(--backdrop);
  }
  .letter {
    position: absolute;
    left: 98px;
    top: 20px;
    width: 828px;
    height: 1160px;
    overflow: hidden;
    color: var(--ink);
    box-shadow: 0 6px 24px rgba(0,0,0,0.18);
  }
  .letter__photo {
    position: absolute;
    inset: 0;
    background: radial-gradient(ellipse at 70% 70%, #c3ccbb 0%, transparent 60%),
                linear-gradient(170deg, var(--paper-tint-a), var(--paper-tint-b));
  }
  .letter__bands { position: absolute; inset: 0; }
  .block { position: absolute; margin: 0; }
  .recipient, .agent-title, .postscript {
    font-family: "Roboto", Arial, sans-serif;
    font-size: 16px;
    line-height: 26px;
  }
  .recipient { left: 88px; top: 124px; }
  .recipient p { margin: 0; }
  .recipient .address { margin-top: 22px; }
  .agent-title { right: 80px; top: 144px; text-align: right; }
  .letter-body {
    left: 88px;
    top: 272px;
    width: 660px;
    font-family: "Didact Gothic", "Century Gothic", sans-serif;
    font-size: 14px;
    line-height: 26px;
  }
  .letter-body p {
    margin: 0 0 24px;
    text-align: justify;
    hyphens: auto;
  }
  .letter-body .salutation { margin-bottom: 22px; }
  .letter-body strong { font-weight: 700; }
  .signature-mark {
    left: 88px;
    top: 856px;
    width: 104px;
    height: 40px;
    border-radius: 4px;
    background: linear-gradient(90deg, rgba(11,79,156,0.35), rgba(11,79,156,0.1));
  }
  .signer {
    left: 88px;
    top: 906px;
    font-family: "EB Garamond", Georgia, serif;
    font-weight: 500;
    font-size: 23px;
    color: var(--brand-blue);
  }
  .signer-phone {
    left: 88px;
    top: 942px;
    font-family: "Roboto", Arial, sans-serif;
    font-size: 15px;
    color: var(--ink-soft);
  }
  .postscript { left: 88px; top: 1012px; width: 680px; }
</style>
</head>
<body>
<main class="letter">
  <div class="letter__photo" role="img" aria-label="Faint photo of two playful bulldogs on green grass"></div>
  <svg class="letter__bands" width="828" height="1160" viewBox="0 0 828 1160" aria-hidden="true">
    <path d="M0 0 H740 C430 10 140 40 0 96 Z" fill="var(--brand-blue)"/>
    <path d="M828 1052 C700 1130 380 1150 60 1160 H828 Z" fill="var(--brand-blue)"/>
  </svg>

  <div class="block recipient">
    <p>Mr Outta State Owner</p>
    <p class="address">12345 Elmwood Street,<br>CEDARVALE FL 30000 0000</p>
  </div>
  <p class="block agent-title">Licensed Real estate agent</p>

  <div class="block letter-body">
    <p class="salutation">Dear Home Owner</p>
    <p>I am writing you because I am interested in purchasing your property located at <strong>123 NE Harbor Ave CEDARVALE FL</strong>. I live nearby in Pinecrest and I Purchase properties throughout the state of Flordia. Currently I am working on projects in the neighborhood, which is how I learned of your property.</p>
    <p>Please call me at . So i can tell you how we can buy your property quickly, with no hassles and most importantly, at a fair price. I purchase the house directly from you, so there are no real estate commissions or extr fees coming out of your pocket. Furthermore, I always make cash offers so you never have to worry about delays resulting from a buyer trying to quality for a morgage and wastingyour valuble time.</p>
    <p>I'll be glad to personally tell you more about how we can work together. All calls are completely confidential and there is no obligation whatsoever. Even if you are not inteested in selling at this time call (555) 0142-0199. So i can help you with derermining the value of your property. You should also keep this letter for further reference. since things in life have a tendency to chagne unexpectedly. Thank you for your time and consideration and I look forward to speaking with you.</p>
    <p>Sincerely,</p>
  </div>

  <div class="block signature-mark" role="img" aria-label="Handwritten signature"></div>
  <p class="block signer">Maren Holloway</p>
  <p class="block signer-phone">(555)0142-01990</p>

  <p class="block postscript">P.S. If you would like to e-mail me information and pictures of your property. please send them to MAREN@hollowhomes.com</p>
</main>
</body>
</html>
```